Foot and ankle surgeon requires a website design

I need a website where prospective and established patients can obtain information and then direct them to making appointments. My practice is a highly professional surgical practice specialising in surgery to the foot and ankle. My title is Mr Colin Brasket, Podiatric Foot & Ankle Surgeon. My qualifications are: BSc MSc FACPS
The practice website will require information on: Locations, phone numbers to make appointments, general background on podiatric surgery,
I would like to include information on: my hospital appointments, surgical fellowships held, training programs undertaken, association memberships, publications written, links to useful websites
A page dedicated to common foot conditions would be useful and also a page with referral information including an online registration section that will be sent direct to the receptionist.
Examples of similar websites include:
http://www.dorvelquintaro.com.au/
http://www.haldenfootsurgeon.com.au/
I will provide files on logo, self photos and my personal training history etc.
Also if there is going to be a background theme I personally am associated with surfing and beach activities, it would be great if this was able to be reflected in the design.
Thank you.

```html
<!DOCTYPE html>
<html lang="en">
<head>
<meta charset="utf-8">
<title>Mr Colin Brasket – Podiatric Foot &amp; Ankle Surgeon</title>
<link rel="stylesheet" href="https://fonts.googleapis.com/css2?family=Gelasio:wght@400;700&family=Arimo:wght@400&display=swap">
<style>
:root{
  --navy:#0e4a8c;
  --navy-dark:#0a3a73;
  --orange:#ec8022;
  --ink:#333;
  --page:#eeeeee;
  --white:#fff;
  --serif:"Gelasio", Georgia, serif;
  --sans:"Arimo", Arial, sans-serif;
}
*{box-sizing:border-box;margin:0;padding:0}
html,body{width:1016px;height:1200px;overflow:hidden}
body{position:relative;background:var(--page);font-family:var(--sans);color:var(--ink)}
.abs{position:absolute}

.site-header{left:0;top:0;width:1016px;height:104px;background:linear-gradient(#fff,#f0f0f0);border-bottom:1px solid #ddd}
.brand{left:130px;top:40px;display:flex;align-items:center;gap:8px}
.brand-dot{width:28px;height:28px;border-radius:50%;background:var(--navy)}
.brand-name{font-family:var(--serif);font-weight:700;font-size:14px;color:var(--navy);line-height:1.2}
.search{left:618px;top:41px;width:217px;height:28px;background:#fff;border:1px solid #ddd;border-radius:3px;font-size:10px;padding:8px 7px;color:#333}
.search svg{position:absolute;right:6px;top:7px}
.social{top:45px;width:20px;height:20px;border-radius:50%;background:var(--navy)}

.hero{left:0;top:104px;width:1016px;height:473px;background:linear-gradient(#cfe3ec 0%,#e6eef0 45%,#e9a58c 62%,#ddd3c3 80%,#e6ded0 100%)}
.hero-title{left:381px;top:185px;font-family:var(--serif);color:var(--orange);line-height:1}
.hero-title .big{font-size:44px;display:block}
.hero-title .small{font-size:30px;display:block;margin-top:4px}
.slider-btn{top:539px;width:30px;height:20px;background:#2a2a2a;display:flex;align-items:center;justify-content:center}

.main-nav{left:100px;top:104px;width:232px;height:473px;background:linear-gradient(#0d4a8c,#0b3f7c)}
.main-nav ul{list-style:none;padding-top:35px}
.main-nav li{height:48px;line-height:48px;padding-left:24px;font-family:var(--serif);font-size:15.5px;color:#fff;border-bottom:1px solid rgba(255,255,255,.06);position:relative}
.main-nav li.active::before{content:"";position:absolute;left:-4px;top:0;width:4px;height:60px;background:var(--orange)}
.main-nav li.active::after{content:"";position:absolute;left:0;top:18px;border:6px solid transparent;border-left-color:var(--orange)}

.feature{left:105px;top:616px;width:499px;height:196px;background:linear-gradient(#8d8d8d,#c9c9c9 55%,#aaa)}
.feature-text{left:117px;top:658px;width:230px;font-family:var(--serif);font-weight:700;font-size:16.5px;line-height:20.5px;color:#0d3f7a}
.intro{left:105px;top:826px;width:510px;font-size:11.6px;line-height:20.4px;color:var(--ink)}

.call{top:1011px;width:160px}
.call-town{font-family:var(--serif);font-weight:700;font-size:12px;color:#333}
.call-phone{font-size:20px;color:#222;margin-top:3px}
.call-btn{display:block;width:138px;height:27px;margin-top:5px;background:var(--orange);border-radius:3px;color:#fff;font-family:var(--serif);font-weight:700;font-size:11px;text-align:center;line-height:27px}

.locations{left:647px;top:616px;width:262px;height:467px;background:#fff;border:1px solid #e2e2e2}
.locations h2{position:absolute;left:17px;top:26px;font-family:var(--serif);font-weight:700;font-size:16.5px;color:var(--navy)}
.loc{position:absolute;left:58px;font-size:10px;line-height:15.2px;color:#333}
.loc b{font-family:var(--serif);font-size:12.5px;color:#222;display:block;line-height:16px}
.loc-icon{position:absolute;left:22px;width:13px;height:13px;background:var(--orange);border-radius:2px}
.contact-line{position:absolute;left:58px;font-size:11.5px;color:#333}
.contact-line b{font-family:var(--serif);font-size:12.5px;margin-right:6px}

.site-footer{left:0;top:1122px;width:1016px;height:78px;background:#f7f7f7;border-top:1px solid #e2e2e2}
.legal{left:112px;top:1155px;font-size:10.5px;color:#222}
.badge{background:#9a9a9a}
</style>
</head>
<body>

<header class="abs site-header">
  <div class="abs brand" style="left:130px;top:42px;position:absolute">
    <span class="brand-dot"></span>
    <span class="brand-name">Mr Colin Brasket</span>
  </div>
  <div class="abs search">Search
    <svg width="14" height="14" viewBox="0 0 14 14"><circle cx="5.5" cy="5.5" r="4" fill="none" stroke="#333" stroke-width="1.6"/><line x1="8.5" y1="8.5" x2="13" y2="13" stroke="#333" stroke-width="2"/></svg>
  </div>
  <span class="abs social" style="left:841px"></span>
  <span class="abs social" style="left:865px"></span>
  <span class="abs social" style="left:889px"></span>
</header>

<section class="abs hero" role="img" aria-label="Photo of a family's bare feet resting on beach sand under a blue sky"></section>
<h1 class="abs hero-title"><span class="big">Foot health</span><span class="small">is a family affair</span></h1>
<span class="abs slider-btn" style="left:849px"><svg width="8" height="10"><polyline points="6,1 2,5 6,9" fill="none" stroke="#fff" stroke-width="2"/></svg></span>
<span class="abs slider-btn" style="left:880px"><svg width="8" height="10"><polyline points="2,1 6,5 2,9" fill="none" stroke="#fff" stroke-width="2"/></svg></span>

<nav class="abs main-nav">
  <ul>
    <li class="active">Home</li>
    <li>Appointments</li>
    <li>Surgical Fellowships</li>
    <li>Training Programs</li>
    <li>Memberships</li>
    <li>Publications</li>
    <li>Useful Websites</li>
    <li>Contact Us</li>
  </ul>
</nav>

<div class="abs feature" role="img" aria-label="Black and white photo of a grandfather and child running along the shoreline"></div>
<p class="abs feature-text">The Heel and Stride Health Group strive to provide exceptional service and care to all patients, young and old, to ensure they enjoy a pain free lifestyle.</p>

<p class="abs intro">For those unfamiliar with our services, we are a team of accredited health professionals dealing with the prevention, diagnosis, treatment and rehabilitation of medical and surgical conditions related to feet, ankles and lower limbs.<br>The Heel and Stride Health Group have practices based throughout regional Western Australia in Geraldton and Kalgoorlie and offer the following services; sports injuries, foot care, foot orthoses and diabetes care. Many foot and lower limb problems, if identified early can be prevented, so take the right step and contact the Heel and Stride Health Group for advice on your foot, ankle, heel or leg pain or sports injury.</p>

<div class="abs call" style="left:105px"><div class="call-town">Geraldton</div><div class="call-phone">08 9900 1472</div><span class="call-btn">Make An Appointment</span></div>
<div class="abs call" style="left:304px"><div class="call-town">Geraldton</div><div class="call-phone">08 9900 2318</div><span class="call-btn">Make An Appointment</span></div>
<div class="abs call" style="left:493px;top:1010px"><div class="call-town">Kalgoorlie</div><div class="call-phone">08 9000 3864</div><span class="call-btn">Make An Appointment</span></div>

<aside class="abs locations">
  <h2>Our Locations</h2>
  <span class="loc-icon" style="top:64px"></span>
  <div class="loc" style="top:60px"><b>Geraldton</b>48 Seabreeze Coastal Road,<br>PO BOX 4720,<br>Geraldton WA 6530<br>Ph: 08 9900 1472<br>Fax: 08 9900 1473</div>
  <span class="loc-icon" style="top:170px"></span>
  <div class="loc" style="top:166px"><b>West End, Geraldton</b>7A &amp; 7B Tidewell Street,<br>Geraldton 6530.<br>Ph: 9900 2318<br>Fax: 9900 2319</div>
  <span class="loc-icon" style="top:263px"></span>
  <div class="loc" style="top:259px"><b>Kalgoorlie</b>3/14 Saltbush St,<br>Kalgoorlie WA 6430<br>Ph: 08 9000 3864<br>Fax: 08 9000 3865</div>
  <svg class="abs" style="left:22px;top:378px" width="15" height="11"><rect x=".5" y=".5" width="14" height="10" fill="none" stroke="#ec8022"/><polyline points="1,1 7.5,6 14,1" fill="none" stroke="#ec8022"/></svg>
  <div class="contact-line" style="top:374px"><b>Email :</b>reception@hshg.com.au</div>
  <span class="loc-icon" style="top:405px;border-radius:50%"></span>
  <div class="contact-line" style="top:402px"><b>Website :</b>www.hshg.com.au</div>
</aside>

<footer class="abs site-footer"></footer>
<p class="abs legal">© Company Name ,All Rights Reserved &nbsp;| Terms Of Service &nbsp;| &nbsp;Privacy Policy</p>
<span class="abs badge" style="left:652px;top:1156px;width:90px;height:10px;border-radius:5px"></span>
<span class="abs badge" style="left:770px;top:1142px;width:30px;height:38px"></span>
<span class="abs badge" style="left:824px;top:1137px;width:58px;height:46px;background:#c8c8c8;border-radius:4px"></span>

</body>
</html>
```